Homemaking training schools needs a Business Card design

Designer, Hello!

No special requirements, good-looking enough.
--------------------------------------------------------------------------

Name: Marcus Dole
Chairman
Tel: 0574-71948263
Mobile: 13857420916
Email: kelvora@mailnest.example
Web: www.prt2019.example
Add: No.258, LanpingJie, BeiyuanQu, Ningbo, Zhejiang

LOGO
Ningbo PRT Homemaking Training School

Target Market(s)

pregnant women, mothers, infants, the elderly and families, including cleaning, cooking, nursing training.

Industry/Entity Type

Business

Contact Information for Business Card

Name: Marcus Dole
Chairman
Tel: 0574-71948263
Mobile: 13857420916
Email: kelvora@mailnest.example
Web: www.prt2019.example

LOGO

Font styles to use
Serif
Sans Serif
Decorative

Requirements
Nice to have
• Feels: clean, specifications, safety, comfort, warmth and happiness.

```html
<!DOCTYPE html>
<html lang="en">
<head>
<meta charset="utf-8">
<title>PuRenTang Business Card</title>
<link href="https://fonts.googleapis.com/css2?family=Roboto:wght@400;700&display=swap" rel="stylesheet">
<style>
  :root {
    --page: #e9e6e1;
    --blue: #1e74c0;
    --magenta: #e2168f;
    --magenta-dark: #a8155f;
    --white: #ffffff;
    --card-light: #f0f0f0;
    --brand-blue: #2a6fb0;
  }
  * { box-sizing: border-box; margin: 0; padding: 0; }
  html, body { width: 1200px; height: 950px; overflow: hidden; }
  body {
    background: var(--page);
    font-family: "Roboto", Arial, sans-serif;
    position: relative;
  }
  .card {
    position: absolute;
    left: 250px;
    width: 700px;
    height: 400px;
    overflow: hidden;
    box-shadow: 0 6px 18px rgba(0,0,0,.18);
  }
  .card--back {
    top: 50px;
    background: linear-gradient(100deg, var(--magenta) 0%, var(--magenta) 55%, var(--magenta-dark) 100%);
  }
  .back-name {
    position: absolute;
    left: 0; right: 0; top: 160px;
    text-align: center;
    color: var(--white);
    font-size: 40px;
    font-weight: 700;
  }
  .back-web {
    position: absolute;
    left: 0; right: 0; top: 250px;
    text-align: center;
    color: rgba(255,255,255,.85);
    font-size: 20px;
    letter-spacing: 3px;
  }
  .card--front {
    top: 500px;
    background: linear-gradient(180deg, var(--white), var(--card-light));
  }
  .contact-panel {
    position: absolute;
    inset: 0;
    background: var(--blue);
    clip-path: polygon(0 0, 55% 0, 44% 100%, 0 100%);
    color: var(--white);
    padding: 38px 0 0 50px;
  }
  .contact-name { font-size: 26px; font-weight: 700; margin-left: 42px; }
  .contact-title { font-size: 17px; margin: 2px 0 0 34px; }
  .contact-address { font-size: 17px; line-height: 1.35; margin: 30px 0 0 20px; }
  .contact-list { list-style: none; margin-top: 8px; font-size: 17px; line-height: 1.45; }
  .contact-list li { display: flex; align-items: center; gap: 10px; }
  .contact-list svg { width: 18px; height: 18px; flex: none; }
  .brand {
    position: absolute;
    left: 430px; right: 20px; top: 176px;
    text-align: center;
    color: var(--brand-blue);
    font-size: 34px;
    font-weight: 700;
  }
</style>
</head>
<body>
  <section class="card card--back" aria-label="Card back">
    <p class="back-name">PuRenTang</p>
    <p class="back-web">www.prt2019.example</p>
  </section>

  <section class="card card--front" aria-label="Card front">
    <div class="contact-panel">
      <p class="contact-name">Marcus Dole</p>
      <p class="contact-title">Chairman</p>
      <p class="contact-address">No.258, LanpingJie<br>BeiyuanQu<br>Ningbo, Zhejiang</p>
      <ul class="contact-list">
        <li>
          <svg viewBox="0 0 24 24" fill="currentColor"><path d="M6.6 10.8a15.1 15.1 0 0 0 6.6 6.6l2.2-2.2a1 1 0 0 1 1-.25 11.4 11.4 0 0 0 3.6.57 1 1 0 0 1 1 1V20a1 1 0 0 1-1 1A17 17 0 0 1 3 4a1 1 0 0 1 1-1h3.5a1 1 0 0 1 1 1c0 1.25.2 2.45.57 3.57a1 1 0 0 1-.25 1z"/></svg>
          0574-71948263
        </li>
        <li>
          <svg viewBox="0 0 24 24" fill="none" stroke="currentColor" stroke-width="2"><rect x="7" y="2" width="10" height="20" rx="2"/><line x1="11" y1="18" x2="13" y2="18"/></svg>
          13857420916
        </li>
        <li>
          <svg viewBox="0 0 24 24" fill="currentColor"><path d="M3 5h18v14H3z"/><path d="M3 5l9 7 9-7" fill="none" stroke="#1e74c0" stroke-width="1.6"/></svg>
          kelvora@mailnest.example
        </li>
        <li>
          <svg viewBox="0 0 24 24" fill="none" stroke="currentColor" stroke-width="2"><circle cx="12" cy="12" r="9"/><path d="M3 12h18M12 3c3 3 3 15 0 18M12 3c-3 3-3 15 0 18"/></svg>
          www.prt2019.example
        </li>
      </ul>
    </div>

    <p class="brand">PuRenTang</p>
  </section>
</body>
</html>
```